Website for Architecture & Interior Design firm

We are architecture and interior design firm looking for website design, word press based, smooth, elegant and easy to use for visitors. It should be easy to navigate using a mobile phone, with the ability to change pictures easily. It is a Bilingual website, (English: left to right, Arabic: right to left). A button in the menu bar is required to change the language, At first, we expect an English version, then we will help the designer by providing Arabic translation for any part of the website. Our website main purpose is to display our works in a picture format (Portfolio) to our clients, which mainly consist of four galleries from our (Services) as follow: 1- Architecture 2- Interior Design 3- Project Management 4- Importing from Abroad - Each service will have its page, which displays projects(items) in thumbnail format with simple text, which deploys (when clicked) into Fullscreen gallery to show the items related pictures (Dark gray or black background). - Navigation buttons/arrows are required, (X) button to close the navigation. - This is a very important part, the user experience in PC/Browser mode or Mobile mode should be easy, error-free and fast. Our homepage consists of four main elements: A- Edge to edge picture (Changing in a smooth transitional way, Random pictures from our Services) with our Logo, also persistent menu bar in the top (Home | About Us | Architecture | Interior design | Project Management | Importing from Abroad) + Social media icons B- Photo tiles (Random pictures from our Services) C- Our Services in a fixed 4-tile picture (Clickable) D- Contact Section (Simple name, contact number, message form) We expect the final service should be: 1- a fully functioning website, WordPress based, ready to be used by visitors 2- full content filling, we will contact the designer and provide the material (texture, text,etc..)
Colors
Designer to choose colors to be used in the design.
Look and feel
Each slider illustrates characteristics of the customer's brand and the style your logo design should communicate.

```html
<!DOCTYPE html>
<html lang="en">
<head>
<meta charset="utf-8">
<title>A &amp; K Studio — Architecture &amp; Interior Design</title>
<link href="https://fonts.googleapis.com/css2?family=Montserrat:wght@300;400;500;600;700;800&display=swap" rel="stylesheet">
<style>
:root{
  --ink:#1f1f1f;
  --text:#333;
  --muted:#666;
  --bar:#262626;
  --navbg:#ececec;
  --page:#efefef;
  --white:#fff;
  --dark:#2a2a2a;
  --teal:#2bb3a0;
}
*{box-sizing:border-box;margin:0;padding:0}
html,body{width:1200px;height:4360px;overflow:hidden;background:var(--page);font-family:'Montserrat',sans-serif;color:var(--text)}
.page{position:relative;width:1200px;height:4360px}
.abs{position:absolute}
.ph{position:absolute}

/* top bar */
.topbar{left:0;top:0;width:1200px;height:41px;background:var(--bar);color:#fff;font-size:13px}
.topbar .mail{left:90px;top:0;height:41px;display:flex;align-items:center;gap:7px;padding:0 12px;border-left:1px solid #444;border-right:1px solid #444;width:190px}
.topbar .right{right:90px;top:0;height:41px;display:flex;align-items:center;gap:16px;font-size:12px}
.topbar .dotico{width:12px;height:12px;border:1.5px solid #fff;border-radius:2px}

/* header */
.header{left:0;top:41px;width:1200px;height:115px;background:var(--white)}
.callus{left:156px;top:30px;display:flex;gap:10px;align-items:center;font-size:17px;color:var(--ink)}
.callus b{display:block;font-weight:600}
.brand{left:0;width:1200px;top:28px;text-align:center;font-size:48px;font-weight:700;letter-spacing:2px;color:var(--ink)}
.search{left:850px;top:30px;display:flex;gap:12px;align-items:center;font-size:17px;color:var(--ink)}

/* nav */
.nav{left:0;top:156px;width:1200px;height:61px;background:var(--navbg);display:flex;align-items:center;font-size:18px;color:var(--ink)}
.nav a{position:absolute;text-decoration:none;color:inherit}
.nav a.active{border-bottom:2px solid var(--ink);padding-bottom:2px}
.nav .close{left:1146px;width:16px;height:16px;border-radius:50%;background:var(--ink)}

/* hero */
.hero{left:0;top:217px;width:1200px;height:582px;background:linear-gradient(180deg,#c9c9c6 0%,#9b9a96 45%,#6e6d6a 75%,#bdbcb8 100%)}
.hero-text{left:0;top:190px;width:1200px;text-align:center;color:#fff}
.hero-text h1{font-size:58px;font-weight:300;line-height:1}
.hero-text h1 b{font-weight:800}
.hero-text p{margin:30px auto 0;width:730px;font-size:18px;font-weight:700;line-height:36px}
.hero-text .cta{margin-top:12px;font-size:17px;font-weight:700;display:inline-flex;gap:8px;align-items:center}

/* about */
.about{left:0;top:799px;width:1200px;height:702px;background:radial-gradient(ellipse at 30% 20%,#fff 0%,#f2f2f2 50%,#e4e4e4 100%)}
.about h2{position:absolute;left:90px;top:200px;font-size:37px;font-weight:400;color:var(--ink)}
.about h2 b{font-weight:700}
.about p{position:absolute;left:91px;top:258px;width:540px;font-size:14px;line-height:34px;text-align:justify;color:var(--text)}
.readmore{left:90px;top:440px;font-size:17px;font-weight:700;color:var(--ink);display:flex;gap:8px;align-items:center}

/* sections */
.title{position:absolute;left:0;width:1200px;text-align:center;font-size:37px;font-weight:400;color:var(--ink)}
.title b{font-weight:700}
.services{left:0;top:1501px;width:1200px;height:834px;background:var(--page)}
.services .lead{position:absolute;left:130px;width:940px;top:146px;text-align:center;font-size:14px;line-height:36px;color:var(--text)}
.tile{position:absolute;top:240px;width:291px;height:437px}
.tile span{position:absolute;left:0;bottom:30px;width:100%;text-align:center;color:#fff;font-weight:700;font-size:17px;letter-spacing:.3px}
.viewmore{left:0;width:1200px;top:714px;text-align:center;font-size:17px;font-weight:700;color:var(--ink)}

.gallery{left:0;top:2335px;width:1200px;height:846px;background:linear-gradient(180deg,#f9f9f9,#ececec)}
.gcell{position:absolute;width:400px;height:264px}
.dots{position:absolute;left:0;width:1200px;display:flex;justify-content:center;gap:6px}
.dots i{width:15px;height:15px;border-radius:50%;border:1.5px solid var(--ink)}
.dots i.on{background:var(--ink)}

.projects{left:0;top:3181px;width:1200px;height:707px;background:var(--page)}
.card{position:absolute;left:242px;top:232px;width:367px;height:193px;background:#fff;padding:22px 10px 0 10px;box-shadow:0 2px 8px rgba(0,0,0,.08)}
.card h3{font-size:20px;font-weight:700;color:var(--ink)}
.card p{margin-top:10px;font-size:11.5px;line-height:27px;text-align:justify;color:var(--muted)}
.arrow{position:absolute;width:54px;height:54px;border-radius:50%;background:var(--ink);display:flex;align-items:center;justify-content:center}
.tdots{position:absolute;left:923px;top:596px;display:flex;gap:4px}
.tdots i{width:14px;height:14px;border-radius:50%;border:1.5px solid var(--teal)}
.tdots i.on{background:var(--teal)}

/* contact */
.contact{left:0;top:3888px;width:1200px;height:388px}
.map{left:0;top:0;width:599px;height:388px;background:linear-gradient(135deg,#dfe7cf 0%,#cfdcb6 40%,#e8e3d2 70%,#d7e1c3 100%)}
.pin{left:272px;top:165px;display:flex;gap:10px;font-size:13.5px;line-height:22px;color:var(--ink)}
.form{left:599px;top:0;width:601px;height:388px;background:var(--dark)}
.field{position:absolute;background:#fff;border:1px solid #ccc;font-size:13.5px;color:#555;padding:12px 8px}
.submit{position:absolute;left:32px;top:273px;width:161px;height:41px;border:2px solid #fff;color:#fff;font-weight:700;font-size:17px;display:flex;align-items:center;justify-content:center}
.rule{position:absolute;left:32px;top:329px;width:479px;height:1px;background:#555}
.cphone{position:absolute;left:32px;top:345px;color:#fff;font-weight:600;font-size:21px;display:flex;gap:8px;align-items:center}
.caddr{position:absolute;left:226px;top:338px;color:#fff;font-size:13px;line-height:21px;display:flex;gap:8px;align-items:center}

.footer{left:0;top:4276px;width:1200px;height:84px;background:#f1f1f1}
.footer .copy{position:absolute;left:0;width:1200px;top:32px;text-align:center;font-size:16px;color:var(--text)}
.footer .social{position:absolute;left:968px;top:24px;display:flex;gap:6px}
.footer .social i{width:32px;height:32px;border-radius:50%;border:1.5px solid var(--ink)}
.footer .ver{position:absolute;left:1145px;top:35px;font-size:11px;color:var(--muted)}
</style>
</head>
<body>
<div class="page">

  <div class="abs topbar">
    <div class="abs mail">
      <svg width="13" height="10" viewBox="0 0 13 10"><rect x=".5" y=".5" width="12" height="9" fill="none" stroke="#fff"/><path d="M.5 .5 6.5 5.5 12.5 .5" fill="none" stroke="#fff"/></svg>
      hello@akstudio.example
    </div>
    <div class="abs right">
      <span>◉ ENG ▾</span>
      <i class="dotico"></i><i class="dotico"></i><i class="dotico"></i><i class="dotico"></i>
    </div>
  </div>

  <header class="abs header">
    <div class="abs callus">
      <svg width="40" height="40" viewBox="0 0 40 40"><circle cx="20" cy="20" r="18" fill="none" stroke="#1f1f1f" stroke-width="2.5"/><path d="M13 11l4 0 2 5-3 2c1 3 3 5 6 6l2-3 5 2 0 4c-9 0-16-7-16-16z" fill="#1f1f1f"/></svg>
      <div>Call us:<b>1-800-555-0142</b></div>
    </div>
    <div class="abs brand">A &amp; K Studio</div>
    <div class="abs search">
      <svg width="42" height="42" viewBox="0 0 42 42"><circle cx="17" cy="17" r="13" fill="none" stroke="#1f1f1f" stroke-width="2.5"/><path d="M27 27l12 12" stroke="#1f1f1f" stroke-width="4"/></svg>
      <div>Search:<br>Enter search here...</div>
    </div>
  </header>

  <nav class="abs nav">
    <a class="active" style="left:103px">HOME</a>
    <a style="left:209px">About Us</a>
    <a style="left:339px">Architecture</a>
    <a style="left:494px">Interior Design</a>
    <a style="left:670px">Project Management</a>
    <a style="left:900px">Importing From Abroad</a>
    <i class="abs close"></i>
  </nav>

  <section class="abs hero" role="img" aria-label="Bright living room interior with grey sofas and a pendant-lit kitchen">
    <div class="abs hero-text">
      <h1>Welcome to <b>A &amp; K Studio</b></h1>
      <p>Lorem ipsum dolor sit amet, consectetur adipiscing elit, sed do eiusmod tempor incididunt ut labore et dolore magna aliqua.</p>
      <div class="cta">Contact Us
        <svg width="16" height="16" viewBox="0 0 16 16"><circle cx="8" cy="8" r="8" fill="#fff"/><path d="M5 8h6M8 5l3 3-3 3" stroke="#555" stroke-width="2" fill="none"/></svg>
      </div>
    </div>
  </section>

  <section class="abs about">
    <h2>About <b>A &amp; K Studio</b></h2>
    <p>Sed ut perspiciatis unde omnis iste natus error sit voluptatem accusantium doloremque laudantium, totam rem aperiam, eaque ipsa quae ab illo inventore veritatis et quasi architecto beatae vitae dicta sunt explicabo. Nemo enim ipsam voluptatem quia voluptas sit aspernatur aut odit aut fugit, sed quia dolores eos qui ratione voluptatem sequi nesciunt.</p>
    <div class="abs readmore">READ MORE
      <svg width="17" height="17" viewBox="0 0 16 16"><circle cx="8" cy="8" r="8" fill="#1f1f1f"/><path d="M5 8h6M8 5l3 3-3 3" stroke="#fff" stroke-width="2" fill="none"/></svg>
    </div>
    <div class="ph" style="left:961px;top:101px;width:149px;height:85px;background:linear-gradient(180deg,#2f5fa8,#c9692b)" role="img" aria-label="Upward view of glass towers at dusk"></div>
    <div class="ph" style="left:665px;top:208px;width:445px;height:270px;background:linear-gradient(135deg,#f4f4f4 0%,#e2e2e2 55%,#8ea4d6 100%)" role="img" aria-label="Modern house blending from pencil sketch to finished building"></div>
    <div class="ph" style="left:575px;top:500px;width:178px;height:102px;background:linear-gradient(135deg,#f7f7f7,#cfcfcf)" role="img" aria-label="Abstract architectural line sketch"></div>
  </section>

  <section class="abs services">
    <h2 class="title" style="top:95px">Our <b>Services</b></h2>
    <p class="lead">Sed ut perspiciatis unde omnis iste natus error sit voluptatem accusantium doloremque laudantium, totam rem aperiam, eaque ipsa quae ab illo inventore veritatis et quasi architecto beatae vitae dicta sunt explicabo.</p>
    <div class="tile" style="left:0;background:linear-gradient(160deg,#e8e6e2,#b9b4ac)" role="img" aria-label="Hands drafting architectural plans"><span>ARCHITECTURE</span></div>
    <div class="tile" style="left:303px;background:linear-gradient(160deg,#c7b49a,#8a8175)" role="img" aria-label="Interior sketch with watercolour palette"><span>INTERIOR DESIGN</span></div>
    <div class="tile" style="left:606px;background:linear-gradient(160deg,#a9a49c,#3e4a55)" role="img" aria-label="Project manager explaining plans in an office"><span>PROJECT MANAGEMENT</span></div>
    <div class="tile" style="left:909px;background:linear-gradient(160deg,#e3e3e1,#a39a8f)" role="img" aria-label="Bright bathroom with imported fixtures"><span>IMPORTING FROM ABROAD</span></div>
    <div class="abs viewmore">VIEW MORE SERVICES
      <svg width="17" height="17" viewBox="0 0 16 16" style="vertical-align:-3px"><circle cx="8" cy="8" r="8" fill="#1f1f1f"/><path d="M5 8h6M8 5l3 3-3 3" stroke="#fff" stroke-width="2" fill="none"/></svg>
    </div>
  </section>

  <section class="abs gallery">
    <h2 class="title" style="top:95px">Our <b>Gallery</b></h2>
    <div class="gcell" style="left:0;top:169px;background:linear-gradient(160deg,#5a8fd1,#d9dde3)" role="img" aria-label="White apartment tower against blue sky"></div>
    <div class="gcell" style="left:400px;top:169px;background:linear-gradient(180deg,#3b6fb8,#9a7c5a 50%,#2d5a9c)" role="img" aria-label="Glass pyramid and palace reflected in water"></div>
    <div class="gcell" style="left:800px;top:169px;background:linear-gradient(160deg,#d8d4cc,#b9aa96)" role="img" aria-label="Designer choosing colour swatches over plans"></div>
    <div class="gcell" style="left:0;top:433px;background:linear-gradient(160deg,#9a9a98,#8bb4c8)" role="img" aria-label="City skyline seen through a concrete window"></div>
    <div class="gcell" style="left:400px;top:433px;background:linear-gradient(180deg,#2b4f8f,#d9c9a8 60%,#2c5c8a)" role="img" aria-label="Modern villa with pool at dusk"></div>
    <div class="gcell" style="left:800px;top:433px;background:linear-gradient(180deg,#5b4a8e,#b46aa0 50%,#1f5fb0)" role="img" aria-label="Waterfront city skyline at twilight"></div>
    <div class="dots" style="top:729px"><i></i><i></i><i class="on"></i></div>
  </section>

  <section class="abs projects">
    <h2 class="title" style="top:95px">Recent <b>Projects</b></h2>
    <div class="ph" style="left:0;top:181px;width:154px;height:394px;background:linear-gradient(160deg,#6a6a70,#3c4a66)" role="img" aria-label="Previous project interior"></div>
    <div class="ph" style="left:206px;top:181px;width:789px;height:394px;background:linear-gradient(180deg,#6fa0d8 0%,#bcd3ea 40%,#8a7a66 75%,#5e7c4a 100%)" role="img" aria-label="Modern two-storey house with timber cladding"></div>
    <div class="ph" style="left:1046px;top:181px;width:154px;height:394px;background:linear-gradient(160deg,#8e8c88,#4a4640)" role="img" aria-label="Next project exterior at dusk"></div>
    <div class="arrow" style="left:179px;top:345px"><svg width="24" height="16" viewBox="0 0 24 16"><path d="M22 8H3M9 2 3 8l6 6" stroke="#fff" stroke-width="2.5" fill="none"/></svg></div>
    <div class="arrow" style="left:966px;top:345px"><svg width="24" height="16" viewBox="0 0 24 16"><path d="M2 8h19M15 2l6 6-6 6" stroke="#fff" stroke-width="2.5" fill="none"/></svg></div>
    <div class="card">
      <h3>Sed ut perspiciatis unde omnis</h3>
      <p>Sed ut perspiciatis unde omnis iste natus error sit voluptatem accusantium doloremque laudantium, totam rem aperiam, eaque ipsa quae ab illo inventore veritatis et quasi architecto beatae vitae dicta sunt explicabo.</p>
    </div>
    <div class="tdots"><i></i><i></i><i class="on"></i><i></i></div>
  </section>

  <section class="abs contact">
    <div class="abs map" role="img" aria-label="Road map of the office area">
      <div class="abs pin">
        <svg width="16" height="22" viewBox="0 0 16 22"><path d="M8 0C3.6 0 0 3.6 0 8c0 6 8 14 8 14s8-8 8-14c0-4.4-3.6-8-8-8z" fill="#e02020"/><circle cx="8" cy="8" r="3" fill="#fff"/></svg>
        <div>Harbor Tower, Palm Street, Meridian City<br>Meridian - 4861203</div>
      </div>
    </div>
    <div class="abs form">
      <div class="field" style="left:32px;top:41px;width:234px;height:41px">First Name</div>
      <div class="field" style="left:278px;top:41px;width:233px;height:41px">Last Name</div>
      <div class="field" style="left:32px;top:97px;width:234px;height:40px">Email</div>
      <div class="field" style="left:278px;top:97px;width:233px;height:40px">Phone Number</div>
      <div class="field" style="left:32px;top:153px;width:479px;height:104px">Message</div>
      <div class="submit">SUBMIT</div>
      <div class="rule"></div>
      <div class="cphone">
        <svg width="18" height="18" viewBox="0 0 18 18"><path d="M3 1h4l2 4-2.5 2c1 2.5 3 4.5 5.5 5.5L14 10l4 2v4c-9 0-15-6-15-15z" fill="#fff"/></svg>
        800 555 0142
      </div>
      <div class="caddr">
        <svg width="16" height="22" viewBox="0 0 16 22"><path d="M8 0C3.6 0 0 3.6 0 8c0 6 8 14 8 14s8-8 8-14c0-4.4-3.6-8-8-8z" fill="#fff"/><circle cx="8" cy="8" r="3" fill="#2a2a2a"/></svg>
        <div>Harbor Tower, Palm Street, Meridian City<br>Meridian - 4861203</div>
      </div>
    </div>
  </section>

  <footer class="abs footer">
    <div class="copy">A &amp; K Studio © 2019. All Rights Reserved.</div>
    <div class="social"><i></i><i></i><i></i><i></i></div>
    <div class="ver">C29</div>
  </footer>

</div>
</body>
</html>
```